Business Card Design - Amberfield Court

We are looking at a new design for our business cards that has a modern and professional look. We run a residential aged care facility focussing on the care of residents. The cards will be used for potential clients, consultants and business opportunities in this sector. Blue and white is our main colours and would to see these colours incorporated in the design.
Industry/Entity Type
Business
Contact Information for Business Card
Amberfield Court, Darren Walsh, dwalsh@amberfieldcourt.com.au, Finance Manager, 0472 639 208, BCom, 37 Marrabel Crescent, Brindle Vale, Qld 4093.
Look and feel
Each slider illustrates characteristics of the customer's brand and the style your logo design should communicate.

```html
<!DOCTYPE html>
<html lang="en">
<head>
<meta charset="utf-8">
<title>Amberfield Court — Business Card</title>
<link rel="stylesheet" href="https://fonts.googleapis.com/css2?family=Open+Sans:wght@400;600;800&display=swap">
<style>
  :root {
    --backdrop: #2b2b2c;
    --taupe: #b1a69c;
    --navy: #1d3a4a;
    --white: #ffffff;
    --ink: #1d3a4a;
    --rule: #b9c6ce;
  }
  * { box-sizing: border-box; margin: 0; padding: 0; }
  html, body { width: 1200px; height: 900px; overflow: hidden; }
  body {
    background: var(--backdrop);
    font-family: "Open Sans", Arial, sans-serif;
    position: relative;
  }
  .card {
    position: absolute;
    width: 620px;
    height: 354px;
    border-radius: 22px;
    overflow: hidden;
  }
  .card--back { left: 110px; top: 60px; background: var(--taupe); }
  .card--front { left: 470px; top: 486px; background: var(--white); }

  .brand {
    position: absolute;
    left: 0; right: 0;
    display: flex;
    justify-content: center;
    align-items: center;
    gap: 12px;
    font-weight: 600;
    font-size: 30px;
    letter-spacing: 3px;
    text-transform: uppercase;
    color: var(--white);
    white-space: nowrap;
  }
  .brand__dot {
    width: 14px; height: 14px;
    border-radius: 50%;
    background: var(--white);
    flex: none;
  }
  .card--back .brand { top: 155px; }

  .front__panel {
    position: absolute;
    left: 0; top: 0;
    width: 100%; height: 228px;
    background: var(--navy);
  }
  .front__rule {
    position: absolute;
    left: 0; top: 220px;
    width: 100%; height: 2px;
    background: var(--rule);
  }
  .card--front .brand { top: 70px; }
  .person {
    position: absolute;
    left: 0; right: 0; top: 144px;
    text-align: center;
    color: var(--white);
  }
  .person__name { font-weight: 800; font-size: 24px; line-height: 1.15; }
  .person__role { font-size: 14px; text-transform: uppercase; line-height: 1.3; }

  .address {
    position: absolute;
    right: 34px; top: 242px;
    text-align: right;
    font-size: 14px;
    font-style: normal;
    line-height: 1.45;
    color: var(--ink);
  }
  .contact {
    position: absolute;
    left: 34px; bottom: 24px;
    list-style: none;
    font-size: 15px;
    line-height: 1.5;
    color: var(--ink);
  }
  .contact li { display: flex; align-items: center; gap: 8px; }
  .contact svg { width: 13px; height: 13px; fill: var(--ink); flex: none; }
</style>
</head>
<body>
  <section class="card card--back" aria-label="Card back">
    <div class="brand"><span class="brand__dot"></span>Amberfield Court</div>
  </section>

  <section class="card card--front" aria-label="Card front">
    <div class="front__panel"></div>
    <div class="front__rule"></div>
    <div class="brand"><span class="brand__dot"></span>Amberfield Court</div>
    <div class="person">
      <p class="person__name">DARREN WALSH</p>
      <p class="person__role">Finance Manager(BCom)</p>
    </div>
    <address class="address">
      37 Marrabel Crescent<br>Brindle Vale, Qld 4093
    </address>
    <ul class="contact">
      <li>
        <svg viewBox="0 0 24 24" aria-hidden="true"><path d="M6.6 10.8a15.1 15.1 0 0 0 6.6 6.6l2.2-2.2a1 1 0 0 1 1-.25 11.4 11.4 0 0 0 3.6.57 1 1 0 0 1 1 1V20a1 1 0 0 1-1 1A17 17 0 0 1 3 4a1 1 0 0 1 1-1h3.5a1 1 0 0 1 1 1c0 1.25.2 2.45.57 3.6a1 1 0 0 1-.25 1z"/></svg>
        0472 639 208
      </li>
      <li>
        <svg viewBox="0 0 24 24" aria-hidden="true"><path d="M2 5h20v14H2zm2 2v.5l8 5 8-5V7zm0 2.9V17h16V9.9l-8 5z"/></svg>
        dwalsh@amberfieldcourt.com.au
      </li>
    </ul>
  </section>
</body>
</html>
```